MRT Property - Business Cards

Looking for a business card & general letterhead, signage etc design for our new logo.

Colours:
000a20
0056a2
00b5ef
0088ce
68cef2

Fonts:
Poppins
Karla

Please keep look and feel of new brand - example in the zip package I sent.

```html
<!DOCTYPE html>
<html lang="en">
<head>
<meta charset="utf-8">
<title>MRT Property – Business Cards</title>
<link rel="stylesheet" href="https://fonts.googleapis.com/css2?family=Poppins:wght@400;500;600&display=swap">
<style>
  :root {
    --page: #1a1a1c;
    --card-dark: #161b2a;
    --navy: #000a20;
    --blue-deep: #0056a2;
    --blue-mid: #0088ce;
    --blue-bright: #00b5ef;
    --blue-pale: #68cef2;
    --grey: #8a8f99;
    --text-light: #e8edf5;
  }
  * { margin: 0; padding: 0; box-sizing: border-box; }
  html, body { width: 1200px; height: 852px; overflow: hidden; }
  body {
    background: var(--page);
    font-family: "Poppins", sans-serif;
    position: relative;
  }
  .card {
    position: absolute;
    top: 271px;
    width: 540px;
    height: 310px;
    border-radius: 22px;
    overflow: hidden;
    background: var(--card-dark);
  }
  .card--back { left: 45px; }
  .card--front { left: 615px; }

  /* back side */
  .back-wordmark {
    position: absolute;
    top: 110px;
    left: 0; right: 0;
    text-align: center;
    font-weight: 600;
    font-size: 46px;
    letter-spacing: 1px;
    color: var(--grey);
  }
  .back-web {
    position: absolute;
    bottom: 36px;
    right: 40px;
    font-size: 11px;
    letter-spacing: 6px;
    color: var(--grey);
  }
  .back-strip {
    position: absolute;
    left: 0; right: 0; bottom: 0;
    height: 14px;
    background: var(--blue-deep);
  }

  /* front side */
  .front-bands { position: absolute; inset: 0; }
  .front-wordmark {
    position: absolute;
    top: 92px;
    left: 30px;
    font-weight: 600;
    font-size: 34px;
    line-height: 1.3;
    color: var(--blue-deep);
  }
  .contact {
    position: absolute;
    top: 158px;
    left: 30px;
    color: var(--text-light);
  }
  .contact-name {
    font-weight: 600;
    font-size: 19px;
    color: var(--blue-bright);
    line-height: 22px;
  }
  .contact-role {
    font-size: 10px;
    line-height: 14px;
    color: var(--text-light);
    margin-bottom: 7px;
  }
  .contact-list { list-style: none; }
  .contact-list li {
    display: flex;
    align-items: center;
    gap: 10px;
    font-size: 12px;
    line-height: 19px;
  }
  .contact-list svg { width: 11px; height: 11px; fill: var(--blue-pale); flex: none; }
  .address {
    position: absolute;
    left: 30px;
    bottom: 13px;
    font-size: 12px;
    line-height: 18px;
    color: var(--text-light);
  }
</style>
</head>
<body>

<section class="card card--back" aria-label="Business card, back">
  <div class="back-wordmark">MRT Property</div>
  <div class="back-web">www.mrtproperty.com</div>
  <div class="back-strip"></div>
</section>

<section class="card card--front" aria-label="Business card, front">
  <svg class="front-bands" viewBox="0 0 540 310" preserveAspectRatio="none" aria-hidden="true">
    <rect x="300" y="42" width="240" height="88" fill="var(--blue-deep)"/>
    <path d="M0 150 H300 Q380 150 430 120 L540 120 V272 H0 Z" fill="var(--blue-deep)"/>
    <path d="M300 150 Q380 150 430 120 L540 120 V150 Z" fill="var(--blue-mid)" opacity="0.35"/>
  </svg>

  <div class="front-wordmark">MRT Property</div>

  <div class="contact">
    <div class="contact-name">Daniel Hartley</div>
    <div class="contact-role">Associate Director</div>
    <ul class="contact-list">
      <li>
        <svg viewBox="0 0 24 24"><path d="M6.6 10.8a15 15 0 0 0 6.6 6.6l2.2-2.2a1 1 0 0 1 1-.25 11.4 11.4 0 0 0 3.6.57 1 1 0 0 1 1 1V20a1 1 0 0 1-1 1A17 17 0 0 1 3 4a1 1 0 0 1 1-1h3.5a1 1 0 0 1 1 1c0 1.25.2 2.45.57 3.6a1 1 0 0 1-.25 1z"/></svg>
        828-555-0147
      </li>
      <li>
        <svg viewBox="0 0 24 24"><path d="M2 5h20v14H2z M2 5l10 8 10-8" fill="none" stroke="var(--blue-pale)" stroke-width="2.5"/></svg>
        daniel@mrtproperty.com
      </li>
      <li>
        <svg viewBox="0 0 24 24"><circle cx="12" cy="12" r="10"/></svg>
        www.mrtproperty.com
      </li>
    </ul>
  </div>

  <div class="address">27 Kestrel Lane Westmere</div>
</section>

</body>
</html>
```